Plakat-Design für kleine deutsche Immobilien- und Reiseveranstalter-Firma
Zielgruppe
Kleine deutsche Immobilien- und Reiseveranstalter-Firma, spezialisiert auf Italien. In Italien sind es Immobilienbesitzer, die aus versch. Gründen hoffen an Ausländer zu verkaufen/vermieten ( Alter ca. ab 35-40)
Aufgabenstellung
Um neue Immo-Besitzer anzusprechen, lassen wir in verschiedenen Gemeinden in der Nordtoskana Plakate gegen Gebühr kleben ( 70 x 100, meistens 1 bis 2 Wochen)
Text auf Italienisch
Was an Text rein muss( falls Sie es anders mitteilen wollen, bin ich gerne bereit es zu diskutieren)
VUOI VENDERE CASA A STRANIERI O AFFITTARLA A TURISTI ? (Übersetzung ca.:= wollen Sie Ihre Immobilie an Ausländer verkaufen oder an Touristen vermieten?)
Verdona
Germania – info@verdona-beispiel.de + 49 7412 3810457
Italia – 0571 – 394062, Cell.: 371 – 2094716, 335- 47 92608,
www.verdonacase-beispiel.com
www.verdonaaffitti-beispiel.com
Der Poster, den man meistens im Vorbeifahren sieht, soll springt sofort ins Auge , fast aufdringlich. Man kann mit Farben oder Bildern (oder beiden) arbeiten. Stechende Farben, sonst minimalistisch einfach. (??)
Erfahrung zeigt, daß die beiden Mobile Nummern (Cell.:) mehr sichtbar sein könnten. Ich kann zwei letzte zeigen, aber ungern, weil sie mir nicht gefallen und Neues – besseres suche.
PS: habe mal so was wie Guerilla -Marketing versucht – wurde nicht verstanden.
Bilder kann ich nach Wunsch liefern.

```html
<!DOCTYPE html>
<html lang="it">
<head>
<meta charset="utf-8">
<title>Verdona – Plakat</title>
<link href="https://fonts.googleapis.com/css2?family=Montserrat:wght@500;600;700;800&display=swap" rel="stylesheet">
<style>
  :root {
    --backdrop: #e9ecef;
    --paper: #ffffff;
    --ink: #111111;
    --dark: #03231f;
    --green: #22b24c;
    --mint: #effcef;
  }
  * { box-sizing: border-box; margin: 0; padding: 0; }
  html, body {
    width: 1200px; height: 1177px; overflow: hidden;
    background: var(--backdrop);
    font-family: "Montserrat", sans-serif;
    color: var(--ink);
  }
  .poster {
    position: absolute; left: 186px; top: 0;
    width: 830px; height: 1177px;
    background: var(--paper);
  }
  .photo { position: absolute; }
  .photo-hero {
    left: 52px; top: 52px; width: 727px; height: 396px;
    background: linear-gradient(180deg, #2f8fd8 0%, #7cbde9 35%, #e9e2d6 48%, #5a9a44 55%, #29c3dc 68%, #1aa6cc 82%, #d8c3a8 100%);
  }
  .photo-bedroom {
    left: 52px; top: 465px; width: 231px; height: 204px;
    background: linear-gradient(160deg, #ece4dc 0%, #d9cfc6 50%, #8f8a88 80%, #b7a898 100%);
  }
  .photo-bathroom {
    left: 299px; top: 465px; width: 232px; height: 204px;
    background: linear-gradient(160deg, #ddd2c2 0%, #b9aa98 50%, #f2f0ee 75%, #a59482 100%);
  }
  .photo-lounge {
    left: 547px; top: 465px; width: 232px; height: 204px;
    background: linear-gradient(170deg, #f1e8e2 0%, #e6d6c8 45%, #eadbc0 70%, #c04a5a 100%);
  }
  .brand {
    position: absolute; left: 52px; top: 728px;
    display: flex; align-items: center; gap: 9px;
  }
  .brand-dot { width: 22px; height: 22px; border-radius: 50%; background: var(--green); }
  .brand-name { font-weight: 700; font-size: 46px; line-height: 60px; letter-spacing: -0.5px; color: var(--ink); }
  .divider {
    position: absolute; left: 307px; top: 708px;
    width: 3px; height: 100px; background: var(--green);
  }
  .headline {
    position: absolute; left: 338px; top: 700px; width: 450px;
    font-weight: 800; font-size: 31px; line-height: 38px;
    text-transform: uppercase; letter-spacing: 0.2px;
  }
  .subline {
    position: absolute; left: 52px; top: 830px; width: 740px;
    font-weight: 500; font-size: 24px; line-height: 34px;
  }
  .contact-row {
    position: absolute; left: 52px; width: 727px; height: 48px;
    display: flex; background: var(--mint);
  }
  .contact-row.de { top: 944px; }
  .contact-row.it { top: 1004px; }
  .country {
    width: 157px; height: 100%; background: var(--dark); color: var(--green);
    font-weight: 700; font-size: 18px; display: flex; align-items: center;
    padding-left: 22px; letter-spacing: 0.5px;
  }
  .contact-row.it .country { letter-spacing: 3px; padding-left: 14px; }
  .contact-items {
    flex: 1; display: flex; align-items: center; gap: 26px; padding-left: 28px;
    font-weight: 500; font-size: 17px;
  }
  .contact-item { display: flex; align-items: center; gap: 12px; white-space: nowrap; }
  .contact-item .sep { color: var(--green); font-weight: 700; }
  .icon { width: 24px; height: 24px; flex: none; }
  .footer-band {
    position: absolute; left: 52px; top: 1070px; width: 727px; height: 56px;
    background: var(--dark); color: #ffffff;
    display: flex; align-items: center; justify-content: space-between;
    padding: 0 22px; font-weight: 500; font-size: 14px;
  }
  .footer-band .hl { color: var(--green); font-weight: 600; }
  .web, .social { display: flex; align-items: center; gap: 9px; white-space: nowrap; }
  .social-square { width: 22px; height: 22px; background: var(--green); border-radius: 3px; }
  .social { font-size: 16px; }
</style>
</head>
<body>
  <main class="poster">
    <div class="photo photo-hero" role="img" aria-label="Villa mit großem Pool, Liegen und Garten unter blauem Himmel"></div>
    <div class="photo photo-bedroom" role="img" aria-label="Helles Schlafzimmer mit Doppelbett"></div>
    <div class="photo photo-bathroom" role="img" aria-label="Modernes Badezimmer mit Aufsatzwaschbecken und Dusche"></div>
    <div class="photo photo-lounge" role="img" aria-label="Wohnbereich mit Ecksofa, Teppich und Dachfenster"></div>

    <div class="brand">
      <span class="brand-dot"></span>
      <span class="brand-name">Verdona</span>
    </div>
    <div class="divider"></div>
    <h1 class="headline">Vuoi vendere casa a stranieri o affittarla a turisti ?</h1>
    <p class="subline">wollen Sie Ihre Immobilie an Ausländer verkaufen oder an Touristen vermieten?</p>

    <section class="contact-row de">
      <div class="country">GERMANIA</div>
      <div class="contact-items">
        <span class="contact-item">
          <svg class="icon" viewBox="0 0 24 24"><rect x="2" y="5" width="20" height="14" fill="none" stroke="#22b24c" stroke-width="2"/><path d="M2 5l10 8 10-8M2 19l8-7M22 19l-8-7" fill="none" stroke="#22b24c" stroke-width="2"/></svg>
          info@verdona-beispiel.de
        </span>
        <span class="contact-item">
          <svg class="icon" viewBox="0 0 24 24"><path d="M6 3l3 4-2 2c1 3 4 6 7 7l2-2 4 3-2 4C10 21 3 14 3 5z" fill="#22b24c"/><path d="M14 3a7 7 0 0 1 7 7M14 7a3 3 0 0 1 3 3" fill="none" stroke="#22b24c" stroke-width="1.8"/></svg>
          + 49 7412 3810457
        </span>
      </div>
    </section>

    <section class="contact-row it">
      <div class="country">ITALIA</div>
      <div class="contact-items">
        <span class="contact-item">
          <svg class="icon" viewBox="0 0 24 24"><path d="M6 3l3 4-2 2c1 3 4 6 7 7l2-2 4 3-2 4C10 21 3 14 3 5z" fill="#22b24c"/><path d="M14 3a7 7 0 0 1 7 7M14 7a3 3 0 0 1 3 3" fill="none" stroke="#22b24c" stroke-width="1.8"/></svg>
          0571 – 394062
        </span>
        <span class="contact-item">
          <svg class="icon" viewBox="0 0 24 24"><rect x="6" y="2" width="12" height="20" rx="2" fill="none" stroke="#22b24c" stroke-width="2"/><circle cx="12" cy="18" r="1.3" fill="#22b24c"/></svg>
          371 – 2094716 <span class="sep">|</span> 335- 47 92608
        </span>
      </div>
    </section>

    <footer class="footer-band">
      <div class="web">
        <svg class="icon" viewBox="0 0 24 24"><circle cx="12" cy="12" r="11" fill="#22b24c"/><g fill="none" stroke="#03231f" stroke-width="1.3"><circle cx="12" cy="12" r="7"/><ellipse cx="12" cy="12" rx="3" ry="7"/><path d="M5 12h14M6 8.5h12M6 15.5h12"/></g></svg>
        <span>www.<span class="hl">verdonacase-beispiel</span>.com <span class="hl">|</span> www.<span class="hl">verdonaaffitti-beispiel</span>.com</span>
      </div>
      <div class="social">
        <span class="social-square"></span>
        <span>verdonacase</span>
      </div>
    </footer>
  </main>
</body>
</html>
```